New Business Card Design Project

Need a design that will create an impact / strong impression towards our clients for our business. We are in the lighting business and we do lighting retrofits for large commercial to industrial clientele.

Target Market(s)

Lighting Industry

Industry/Entity Type

Business

Font styles to use
Other font styles liked:
• we would like to use the font on our logo, not sure what it is though..

Requirements
Must have
• Our logo.
Nice to have
• We are open to suggestions that have to do with lighting.

```html
<!DOCTYPE html>
<html lang="en">
<head>
<meta charset="utf-8">
<title>Lumenway Retrofit Co. — Business Card</title>
<link rel="stylesheet" href="https://fonts.googleapis.com/css2?family=Lato:wght@400;700&display=swap">
<style>
  :root {
    --stage: #000000;
    --green-deep: #0b4a1a;
    --green-base: #0f7a2e;
    --green-mid: #0a8437;
    --green-bright: #6cc95a;
    --green-dark: #153a12;
    --ink: #ffffff;
  }
  html, body {
    margin: 0;
    padding: 0;
    width: 1200px;
    height: 900px;
    overflow: hidden;
    background: var(--stage);
  }
  .canvas {
    position: relative;
    width: 1200px;
    height: 900px;
    font-family: "Lato", Arial, sans-serif;
    color: var(--ink);
  }
  .card-art {
    position: absolute;
    left: 0;
    top: 0;
  }
  .card-front-text {
    position: absolute;
    left: 140px;
    top: 304px;
  }
  .holder-name {
    font-size: 19px;
    font-weight: 700;
    margin: 0;
    line-height: 1.2;
  }
  .holder-title {
    font-size: 13.5px;
    margin: 1px 0 0;
  }
  .address {
    font-size: 13.5px;
    line-height: 17px;
    margin: 12px 0 0;
    font-style: normal;
  }
  .contact-list {
    list-style: none;
    padding: 0;
    margin: 11px 0 0;
    font-size: 13.5px;
    line-height: 17px;
  }
  .contact-list li {
    display: flex;
    align-items: center;
    gap: 7px;
  }
  .contact-list svg {
    width: 11px;
    height: 11px;
    fill: var(--ink);
    flex: none;
  }
  .brand-name {
    position: absolute;
    left: 760px;
    top: 486px;
    width: 310px;
    margin: 0;
    font-size: 26px;
    font-weight: 700;
    letter-spacing: 0.3px;
    line-height: 1.1;
    text-align: right;
    white-space: nowrap;
  }
</style>
</head>
<body>
<main class="canvas">
  <svg class="card-art" width="1200" height="900" viewBox="0 0 1200 900">
    <defs>
      <radialGradient id="front-glow" cx="0.92" cy="0.1" r="1">
        <stop offset="0" stop-color="#5dbd55"/>
        <stop offset="0.35" stop-color="#0d7d2f"/>
        <stop offset="1" stop-color="#0b4a1a"/>
      </radialGradient>
      <radialGradient id="back-glow" cx="0.6" cy="0.15" r="0.9">
        <stop offset="0" stop-color="#14863a"/>
        <stop offset="1" stop-color="#0b4d1c"/>
      </radialGradient>
      <linearGradient id="front-accent" x1="0" y1="1" x2="1" y2="0">
        <stop offset="0" stop-color="#0a8437" stop-opacity="0"/>
        <stop offset="0.45" stop-color="#0a8437" stop-opacity="0.7"/>
        <stop offset="1" stop-color="#6cc95a" stop-opacity="0.85"/>
      </linearGradient>
      <linearGradient id="back-accent" x1="0" y1="0" x2="1" y2="0">
        <stop offset="0" stop-color="#0a8437"/>
        <stop offset="1" stop-color="#153a12"/>
      </linearGradient>
      <clipPath id="front-shape">
        <path d="M116 275 H548 A45 45 0 0 1 593 320 V568 H161 A45 45 0 0 1 116 523 Z"/>
      </clipPath>
      <clipPath id="back-shape">
        <path d="M667 275 H1099 V523 A45 45 0 0 1 1054 568 H622 V320 A45 45 0 0 1 667 275 Z"/>
      </clipPath>
    </defs>

    <g class="card-front" clip-path="url(#front-shape)">
      <rect x="116" y="275" width="477" height="293" fill="url(#front-glow)"/>
      <rect class="front-accent" x="267" y="376" width="326" height="192" fill="url(#front-accent)"
            role="img" aria-label="Decorative brand mark area"/>
    </g>

    <g class="card-back" clip-path="url(#back-shape)">
      <rect x="622" y="275" width="477" height="293" fill="url(#back-glow)"/>
      <rect class="back-accent" x="622" y="275" width="161" height="293" fill="url(#back-accent)"
            role="img" aria-label="Decorative brand mark band"/>
    </g>
  </svg>

  <section class="card-front-text">
    <h1 class="holder-name">Daniel Harper</h1>
    <p class="holder-title">Managing Director</p>
    <address class="address">4820 Harbor Light Avenue<br>Portland, 97201.</address>
    <ul class="contact-list">
      <li><svg viewBox="0 0 24 24"><path d="M6.6 10.8a15 15 0 0 0 6.6 6.6l2.2-2.2c.3-.3.7-.4 1-.2 1.1.4 2.3.6 3.6.6.6 0 1 .4 1 1V20c0 .6-.4 1-1 1A17 17 0 0 1 3 4c0-.6.4-1 1-1h3.5c.6 0 1 .4 1 1 0 1.3.2 2.5.6 3.6.1.3 0 .7-.2 1z"/></svg>044-555 018 246</li>
      <li><svg viewBox="0 0 24 24"><path d="M2 5h20L12 12z M2 7l10 7 10-7v12H2z"/></svg>hello@lumenway.com</li>
      <li><svg viewBox="0 0 24 24"><path d="M10 14a4 4 0 0 0 5.7 0l4-4a4 4 0 0 0-5.7-5.7l-1.5 1.5 1.4 1.4 1.5-1.5a2 2 0 0 1 2.9 2.9l-4 4a2 2 0 0 1-2.9 0zM14 10a4 4 0 0 0-5.7 0l-4 4a4 4 0 0 0 5.7 5.7l1.5-1.5-1.4-1.4-1.5 1.5a2 2 0 0 1-2.9-2.9l4-4a2 2 0 0 1 2.9 0z"/></svg>www.lumenway.com</li>
    </ul>
  </section>

  <p class="brand-name">Lumenway Retrofit Co.</p>
</main>
</body>
</html>
```